Product brochure for RTG Plans and Voip Telephone Systems

Our company recently added RTG internet and fuly managed cloud hosted VOIP telephony system into our product line. We need a brochure designed that we can put on our website and also print out and take to potential client meetings to showcase our offiering. The brochure will need to describe our details of our voip system and 3 RTG speed offering along with pricing. This brochure will also need to incorporate our company logo which can be found on our website www.coppervale.com.au
We are essentially looking for an overall brochure template that we can add in the details and pricing after. Winning designer will need to provide all original modifiable vectors/files. We would also like to turn the winning design into a template for a page on our website to showcase our product.
Our 7KV voip telephone system is used by some of the largest corporations in the world. More details can be found at 7kv.com
Target Market(s)
Small to medium businesses and large enterprises.
Industry/Entity Type
Internet
Look and feel

```html
<!DOCTYPE html>
<html lang="en">
<head>
<meta charset="utf-8">
<title>Coppervale Technology – RTG Plans and VOIP Brochure Spread</title>
<link href="https://fonts.googleapis.com/css2?family=Open+Sans:ital,wght@0,400;0,600;0,700;1,600&display=swap" rel="stylesheet">
<style>
:root{
  --red:#c4161c;
  --red-dark:#9e1015;
  --charcoal:#2a2a2c;
  --ink:#3a3a3a;
  --paper:#fbfbfc;
  --paper-shade:#eef0f3;
  --backdrop:#d9dadc;
  --photo-a:#cfd6de;
  --photo-b:#8a7a6c;
}
*{box-sizing:border-box;margin:0;padding:0}
html,body{width:1200px;height:789px;overflow:hidden;background:var(--backdrop);font-family:"Open Sans",Arial,sans-serif;color:var(--ink)}
.spread{position:absolute;left:30px;top:20px;width:1140px;height:749px;display:flex;box-shadow:0 6px 24px rgba(0,0,0,.25)}
.page{position:relative;width:570px;height:749px;background:linear-gradient(135deg,var(--paper),var(--paper-shade));overflow:hidden}
.page--left{box-shadow:inset -18px 0 20px -16px rgba(0,0,0,.25)}
.page--right{box-shadow:inset 18px 0 20px -16px rgba(0,0,0,.25)}

/* left page */
.hero-photo{position:absolute;left:0;top:0;width:570px;height:372px;background:linear-gradient(120deg,var(--photo-a) 0%,#e6e9ec 35%,var(--photo-b) 75%,#5d4b40 100%)}
.hero-banner{position:absolute;left:0;top:262px;width:330px;height:96px;background:var(--red);color:#fff;padding:16px 20px 0 28px;font-style:italic;font-weight:600;font-size:18px;line-height:1.3}
.intro{position:absolute;left:28px;top:390px;width:514px;font-size:11px;line-height:1.5}
.region-heading{position:absolute;left:28px;top:482px;width:514px;color:var(--red);font-weight:700;font-size:18px;line-height:1.3}
.region-copy{position:absolute;left:28px;top:540px;width:514px;font-size:11px;line-height:1.5}

.footer{position:absolute;left:0;bottom:0;width:570px;height:64px}
.footer-band{position:absolute;inset:0;width:100%;height:100%}
.footer-phone,.footer-web{position:absolute;top:0;height:64px;display:flex;align-items:center;white-space:nowrap}
.footer-phone{color:#fff;font-weight:600;font-size:15px;letter-spacing:.5px;gap:8px}
.footer-web{color:#fff;font-size:13px}
.phone-icon{flex:none;width:18px;height:18px}
.page--left .footer-phone{left:26px}
.page--left .footer-web{right:36px}
.page--right .footer-web{left:40px}
.page--right .footer-phone{right:28px}

/* right page */
.services-tab{position:absolute;left:38px;top:0;width:220px;height:48px;background:var(--red);color:#fff;font-weight:700;font-size:22px;display:flex;align-items:center;justify-content:center}
.col{position:absolute;top:64px;width:240px}
.col--a{left:38px}
.col--b{left:298px;top:108px}
.service{margin-bottom:16px}
.service-head{display:flex;align-items:center;gap:8px;color:var(--red);font-size:15px;font-weight:600;line-height:1.15;margin-bottom:5px}
.service-icon{flex:none;width:30px;height:30px}
.service-desc{font-size:9px;line-height:1.4;margin-bottom:4px}
.ticks{list-style:none;font-size:9.5px;line-height:1.42}
.ticks li{position:relative;padding-left:14px}
.ticks li::before{content:"";position:absolute;left:2px;top:3px;width:7px;height:4px;border-left:2px solid var(--red);border-bottom:2px solid var(--red);transform:rotate(-45deg)}
.plan-price{color:var(--red);font-weight:700}
</style>
</head>
<body>
<main class="spread">

  <section class="page page--left">
    <div class="hero-photo" role="img" aria-label="Photograph of four business people gathered around a laptop in a bright office"></div>
    <h1 class="hero-banner">Intelligent, Straightforward Business IT Support in Darwin and Surrounds</h1>
    <p class="intro">COPPERVALE Technology is Darwin's 1st choice IT services provider. Businesses are relying more and more on technology to get the job done in the modern age. As a result, you need a quality provider of IT services to ensure you minimise downtime, smooth over inefficiencies and stay productive. Coppervale Tech has more than 15 years' experience and is the team to call to stay competitive in the ever-evolving world of technology.</p>
    <h2 class="region-heading">Offering IT Services Throughout Darwin, Wulagi, Palmerston, Humpy Doo and Beyond</h2>
    <p class="region-copy">Whether you need contracted onsite technicians or project staffing, want to set up cloud-based capabilities, would like to install OfficeSuite or integrate FieldDesk or setup a VOIP / SIP Telephony System or need anything else, our team of IT professionals will put the needs of your business first. We do this by focusing our approach on "Growth Through Technology" and strive to streamline all your processes to maximise productivity. Regardless of the industry you operate in, COPPERVALE Tech will provide you with an affordable solution.</p>
    <footer class="footer">
      <svg class="footer-band" viewBox="0 0 570 64" preserveAspectRatio="none" aria-hidden="true">
        <polygon points="0,0 300,0 330,64 0,64" fill="var(--red)"/>
        <polygon points="300,0 570,0 570,64 330,64" fill="var(--charcoal)"/>
        <polygon points="290,0 300,0 330,64 320,64" fill="var(--red-dark)"/>
      </svg>
      <div class="footer-phone">
        <svg class="phone-icon" viewBox="0 0 18 18" aria-hidden="true"><circle cx="9" cy="9" r="8" fill="none" stroke="#fff" stroke-width="1.4"/><path d="M6 5c-.6.6-.6 2 .8 4s3 3.2 4 3.2l1-1-1.5-1.3-.8.6c-.7-.3-1.7-1.3-2-2l.6-.8L6.9 4.9z" fill="#fff"/></svg>
        (08) 8123 4560
      </div>
      <div class="footer-web">www.coppervale.com.au</div>
    </footer>
  </section>

  <section class="page page--right">
    <h2 class="services-tab">Our Services</h2>

    <div class="col col--a">
      <article class="service">
        <h3 class="service-head"><svg class="service-icon" viewBox="0 0 30 30" aria-hidden="true"><polygon points="15,1 28,8 28,22 15,29 2,22 2,8" fill="#fff" stroke="var(--red)" stroke-width="1.5"/><rect x="9" y="10" width="12" height="8" fill="none" stroke="var(--charcoal)" stroke-width="1.5"/><line x1="7" y1="20" x2="23" y2="20" stroke="var(--charcoal)" stroke-width="1.5"/></svg>Technical Support</h3>
        <p class="service-desc">We deliver IT support for businesses of all sizes in the Top End. We have a range of services available to offer our clients.</p>
        <ul class="ticks"><li>PC \ Laptop Support</li><li>Server Support</li><li>Printers</li><li>Networking</li><li>Business On Site Support</li><li>Virus \ SPAM Removal</li></ul>
      </article>
      <article class="service">
        <h3 class="service-head"><svg class="service-icon" viewBox="0 0 30 30" aria-hidden="true"><polygon points="15,1 28,8 28,22 15,29 2,22 2,8" fill="#fff" stroke="var(--red)" stroke-width="1.5"/><rect x="8" y="11" width="14" height="8" rx="1" fill="none" stroke="var(--charcoal)" stroke-width="1.5"/><line x1="10" y1="15" x2="20" y2="15" stroke="var(--charcoal)" stroke-width="1.2" stroke-dasharray="1.5 1"/></svg>IT Solutions</h3>
        <p class="service-desc">Let us take the headache of IT support from your hands. COPPERVALE Technology has extensive support expertise including servers, PCs, Printers and Network.</p>
        <ul class="ticks"><li>System Monitoring</li><li>System Administration</li><li>Winstack Server Maintenance</li><li>Backup Solution</li><li>Infrastructure Consultation, Design and Implementation</li><li>IT Outsourcing</li></ul>
      </article>
      <article class="service">
        <h3 class="service-head"><svg class="service-icon" viewBox="0 0 30 30" aria-hidden="true"><polygon points="15,1 28,8 28,22 15,29 2,22 2,8" fill="#fff" stroke="var(--red)" stroke-width="1.5"/><path d="M10 9c-1 1-1 4 1.5 7.5s5.5 5 7 5l1.5-1.5-2.5-2.2-1.3 1c-1.2-.5-3-2.3-3.5-3.5l1-1.3L11.5 8.5z" fill="var(--charcoal)"/></svg>7KV Cloud VOIP Telephony</h3>
        <p class="service-desc">Our fully managed, cloud hosted 7KV VOIP telephone system is used by some of the largest corporations in the world, and is set up and supported locally by COPPERVALE Technology.</p>
        <ul class="ticks"><li>Fully Managed &amp; Cloud Hosted</li><li>Desk Phones, Softphones &amp; Mobile App</li><li>Auto Attendant, Queues &amp; Voicemail to Email</li><li>Keep Your Existing Numbers</li><li>From <span class="plan-price">$XX</span> per user / month</li></ul>
      </article>
    </div>

    <div class="col col--b">
      <article class="service">
        <h3 class="service-head"><svg class="service-icon" viewBox="0 0 30 30" aria-hidden="true"><polygon points="15,1 28,8 28,22 15,29 2,22 2,8" fill="#fff" stroke="var(--red)" stroke-width="1.5"/><rect x="8" y="9" width="6" height="12" fill="none" stroke="var(--charcoal)" stroke-width="1.5"/><rect x="15" y="11" width="8" height="6" fill="none" stroke="var(--charcoal)" stroke-width="1.5"/></svg>IT Services</h3>
        <p class="service-desc">COPPERVALE Technology provides a full range of IT Services to suit your business need. We strive to keep your business IT System operating.</p>
        <ul class="ticks"><li>Hardware Sales</li><li>VPN \ Remote Access</li><li>Winstack Server Installation</li><li>Antivirus &amp; SPAM</li><li>Retail Systems</li><li>Software Package Upgrade</li><li>System Integrations</li></ul>
      </article>
      <article class="service">
        <h3 class="service-head"><svg class="service-icon" viewBox="0 0 30 30" aria-hidden="true"><polygon points="15,1 28,8 28,22 15,29 2,22 2,8" fill="#fff" stroke="var(--red)" stroke-width="1.5"/><path d="M8 13a10 10 0 0 1 14 0M10.5 16a6 6 0 0 1 9 0" fill="none" stroke="var(--charcoal)" stroke-width="1.5"/><circle cx="15" cy="19.5" r="1.6" fill="var(--charcoal)"/></svg>RTG Business Internet</h3>
        <p class="service-desc">Fast, reliable RTG internet for your business, with three speed plans to choose from and local support when you need it:</p>
        <ul class="ticks"><li>Standard 25/10 Mbps – <span class="plan-price">$XX</span> / month</li><li>Business 50/20 Mbps – <span class="plan-price">$XX</span> / month</li><li>Premium 100/40 Mbps – <span class="plan-price">$XX</span> / month</li><li>Unlimited data, no lock-in contract</li></ul>
      </article>
      <article class="service">
        <h3 class="service-head"><svg class="service-icon" viewBox="0 0 30 30" aria-hidden="true"><polygon points="15,1 28,8 28,22 15,29 2,22 2,8" fill="#fff" stroke="var(--red)" stroke-width="1.5"/><circle cx="15" cy="12" r="3.5" fill="var(--charcoal)"/><path d="M8 22c1-5 13-5 14 0z" fill="var(--charcoal)"/></svg>Staffing Solutions</h3>
        <p class="service-desc">From full office setup to long term deployment at world class Oil &amp; Gas and Mining projects, COPPERVALE Technology can quickly mobilise resources to your project wherever they are needed, all across Australia. Previous deployment locations include Bladin Point, Nhulunbuy &amp; Alice Springs N.T, Gladstone, Mt. Isa &amp; Cloncurry QLD, Port Hedland WA.</p>
        <ul class="ticks"><li>Long or Short Term Deployment</li><li>Contract Placements for Projects</li><li>Workforce-as-a-Service</li><li>Fully Outsourced / Fast Mobilisation</li><li>Dedicated Consultant</li></ul>
      </article>
    </div>

    <footer class="footer">
      <svg class="footer-band" viewBox="0 0 570 64" preserveAspectRatio="none" aria-hidden="true">
        <polygon points="0,0 240,0 270,64 0,64" fill="var(--charcoal)"/>
        <polygon points="240,0 570,0 570,64 270,64" fill="var(--red)"/>
        <polygon points="0,0 22,0 22,64 0,64" fill="var(--red)"/>
      </svg>
      <div class="footer-web">www.coppervale.com.au</div>
      <div class="footer-phone">
        <svg class="phone-icon" viewBox="0 0 18 18" aria-hidden="true"><circle cx="9" cy="9" r="8" fill="none" stroke="#fff" stroke-width="1.4"/><path d="M6 5c-.6.6-.6 2 .8 4s3 3.2 4 3.2l1-1-1.5-1.3-.8.6c-.7-.3-1.7-1.3-2-2l.6-.8L6.9 4.9z" fill="#fff"/></svg>
        (08) 8123 4560
      </div>
    </footer>
  </section>

</main>
</body>
</html>
```